Property management company looking for modern card design

We at Blue Heron Partners provides property management services for its residential and commercial properties, with expertise in all categories of multifamily, industrial and office projects throughout California.

We need a business card design that is professional and modern designed business card. In our field, clients get hundreds of business cards, we would like our card to stand out.

Please avoid small print.

Target Market(s)

Professionals and high end clients

Industry/Entity Type

Financial Planning

Contact Information for Business Card

Company Name: Blue Heron Partners, Name, email, license #, phone number, website blueheronpartners.com

Font styles to use
Sans Serif

Requirements
Must have
• The card design needs to be adaptable because there is a possibly we will be expanding into different sectors other than real estate. The card design should be focused on financial planning and asset management.
Nice to have
• Modern and simple business card. Eye catching. Non-standard size/shaped cards would be great.
• blueheronpartners.com
Should not have
• Too many bright color or any pictures or shapes of real estate stuff.

```html
<!DOCTYPE html>
<html lang="en">
<head>
<meta charset="utf-8">
<title>Blue Heron Partners – Business Card</title>
<link rel="stylesheet" href="https://fonts.googleapis.com/css2?family=PT+Sans:wght@400&display=swap">
<style>
  :root {
    --page-bg: #1c1f1a;
    --card-black: #050505;
    --card-sheen: #2a2a2a;
    --brand-red: #d81e2a;
    --brand-red-deep: #8e0f16;
    --name-red: #b8323a;
    --text-light: #d9d9d9;
    --mark-neutral: #3a3a3a;
    --divider: #3a1a1c;
  }
  * { margin: 0; padding: 0; box-sizing: border-box; }
  html, body {
    width: 1200px; height: 952px; overflow: hidden;
    background: var(--page-bg);
    font-family: "PT Sans", "Helvetica Neue", Arial, sans-serif;
  }
  .canvas {
    position: relative; width: 1200px; height: 952px;
    display: flex; flex-direction: column; align-items: center; justify-content: center; gap: 52px;
  }
  .card {
    position: relative; width: 700px; height: 400px; overflow: hidden;
    border-radius: 6px;
    background: linear-gradient(160deg, var(--card-sheen) 0%, var(--card-black) 45%, var(--card-black) 100%);
    box-shadow: 0 10px 30px rgba(0,0,0,.55);
  }
  /* Back */
  .card-back { display: flex; flex-direction: column; align-items: center; justify-content: center; gap: 26px; }
  .brand-mark {
    width: 56px; height: 56px; border-radius: 50%;
    background: var(--mark-neutral);
  }
  .brand-name {
    color: var(--brand-red); font-size: 38px; letter-spacing: 8px; text-transform: uppercase;
  }
  /* Front */
  .front-brand {
    position: absolute; left: 0; top: 0; width: 300px; height: 340px;
    display: flex; flex-direction: column; align-items: center; justify-content: center; gap: 22px;
  }
  .front-brand .brand-mark { width: 44px; height: 44px; }
  .front-brand .brand-name { font-size: 25px; letter-spacing: 5px; text-align: center; line-height: 1.3; }
  .divider {
    position: absolute; left: 300px; top: 22px; width: 1px; height: 300px;
    background: linear-gradient(to bottom, transparent, var(--divider) 20%, var(--divider) 80%, transparent);
  }
  .holder-name {
    position: absolute; left: 334px; top: 40px;
    color: var(--name-red); font-size: 32px;
  }
  .contact-list {
    position: absolute; left: 334px; top: 170px; list-style: none;
    display: flex; flex-direction: column; gap: 12px;
  }
  .contact-item { display: flex; align-items: center; gap: 14px; color: var(--text-light); font-size: 27px; }
  .contact-icon {
    width: 30px; height: 30px; border-radius: 5px; background: var(--brand-red);
    display: flex; align-items: center; justify-content: center; flex: none;
  }
  .license-band {
    position: absolute; left: 0; bottom: 0; width: 100%; height: 60px;
    background: linear-gradient(to right, var(--brand-red-deep), var(--brand-red));
    display: flex; align-items: center; justify-content: center;
    color: var(--text-light); font-size: 26px;
  }
</style>
</head>
<body>
<main class="canvas">
  <section class="card card-back">
    <div class="brand-mark"></div>
    <div class="brand-name">Blue Heron Partners</div>
  </section>

  <section class="card card-front">
    <div class="front-brand">
      <div class="brand-mark"></div>
      <div class="brand-name">Blue Heron<br>Partners</div>
    </div>
    <div class="divider"></div>
    <div class="holder-name">Evan Marlowe</div>
    <ul class="contact-list">
      <li class="contact-item">
        <span class="contact-icon">
          <svg width="18" height="18" viewBox="0 0 24 24"><path fill="#fff" d="M6.6 10.8a15 15 0 0 0 6.6 6.6l2.2-2.2a1 1 0 0 1 1-.25 11.4 11.4 0 0 0 3.6.57 1 1 0 0 1 1 1V20a1 1 0 0 1-1 1A17 17 0 0 1 3 4a1 1 0 0 1 1-1h3.5a1 1 0 0 1 1 1c0 1.25.2 2.45.57 3.57a1 1 0 0 1-.25 1z"/></svg>
        </span>972-555-0148
      </li>
      <li class="contact-item">
        <span class="contact-icon">
          <svg width="18" height="14" viewBox="0 0 24 18"><rect x="1" y="1" width="22" height="16" rx="1" fill="#fff"/><path d="M1 2l11 8 11-8" fill="none" stroke="#d81e2a" stroke-width="2"/></svg>
        </span>evan@blueheron.com
      </li>
      <li class="contact-item">
        <span class="contact-icon">
          <svg width="18" height="18" viewBox="0 0 24 24" fill="none" stroke="#fff" stroke-width="1.8"><circle cx="12" cy="12" r="10"/><ellipse cx="12" cy="12" rx="4.5" ry="10"/><path d="M2 12h20M4 6.5h16M4 17.5h16"/></svg>
        </span>blueheronpartners.com
      </li>
    </ul>
    <div class="license-band">Lic : 20481736</div>
  </section>
</main>
</body>
</html>
```